Nanny Share Ecommerce Website for Finding Childcare and Parents who need Childcare BrightPramHub.net

Our company needs an ecommerce website (BrightPramHub.net) for a US subscription based service strictly for nanny sharing that connects families and caregivers. The website would allow families to connect with one another as well as to search for nannies. The service would be searchable for other families by location (by radius or zip code), children demographic (age range/gender/special needs), days of week or times, after school care, school closure days (holidays), etc. The service would also be searchable for nannies based on gender, provider age range, years experience, language, hourly rate, transportation available, certification (CPR first aid), education etc. The search fields would be searchable and sortable and allow to connect with the provider (after paying subscription fee). The service would be similar to tendlyfolk.net in that it would allow for families and caregivers to post photos as well as a short bio of the themselves. There would also be a feedback/star rating mechanism to rate caregivers who have performed work for families (viewable to public). The service would be free for nannies to post their bios and only a subscription based service for families to connect with other families or with caregivers (able to view bio but need service to connect). There will be a short bio on the benefits of nanny sharing (reduced cost, increased flexibility for parents, reduced illness, increased socialization with other children vs. sole nanny), as well as Q&A section with best practices.

Target Market(s)

Families, Nannies

Industry/Entity Type

Childcare

Logo Text

Bright Pram Hub

Coding

Coded - Design and coding required

Number of Pages Required

5+ page

Requirements
Must have
• Searchable (need to be able to search for families as well as nannies), responsive, functional, easy to use, add value to families and nannies. Needs to be able to collect payment for subscription.
Nice to have
• Optimized for mobile, SEO optimized

```html
<!DOCTYPE html>
<html lang="en">
<head>
<meta charset="utf-8">
<title>Bright Pram Hub – Nanny Sharing</title>
<link href="https://fonts.googleapis.com/css2?family=Poppins:wght@400;500;600&family=Open+Sans:ital,wght@0,400;0,600;1,600&display=swap" rel="stylesheet">
<style>
:root{
  --pink:#f06c7e;
  --pink-dark:#e85a6d;
  --cyan:#1bb8e3;
  --blush:#fdeef0;
  --ink:#2b2b2b;
  --text:#555;
  --mist:#f1f1f1;
  --night:#161616;
  --white:#fff;
}
*{box-sizing:border-box;margin:0;padding:0}
html,body{width:1200px;height:3564px;overflow:hidden}
body{font-family:"Open Sans",sans-serif;color:var(--text);background:var(--white);position:relative}
h1,h2,h3,h4{font-family:"Poppins",sans-serif;font-weight:500}
.btn{display:inline-block;font-family:"Poppins",sans-serif;font-size:14px;color:var(--white);padding:9px 16px;border-radius:3px;box-shadow:0 3px 0 rgba(0,0,0,.15)}
.btn-pink{background:var(--pink)}
.btn-cyan{background:var(--cyan)}
.eyebrow{font-family:"Poppins",sans-serif;font-size:16px;color:var(--cyan)}
.section-title{font-size:33px;color:var(--pink);line-height:1.2}
.center{text-align:center}

/* header */
.site-header{position:absolute;top:0;left:0;width:1200px;height:95px}
.brand{position:absolute;left:100px;top:22px;display:flex;align-items:center;gap:10px;font-family:"Poppins",sans-serif;font-weight:600;font-size:22px;color:var(--cyan)}
.brand-dot{width:34px;height:34px;border-radius:50%;background:var(--cyan)}
.join{position:absolute;left:1005px;top:10px;padding:6px 16px;font-size:14px}
.main-nav{position:absolute;right:100px;top:53px;display:flex;gap:33px;font-family:"Poppins",sans-serif;font-size:16px;color:var(--ink)}
.main-nav .active{color:var(--pink)}

/* hero */
.hero{position:absolute;top:95px;left:0;width:1200px;height:513px}
.hero-photo{position:absolute;inset:0;background:linear-gradient(100deg,#8a8c7c 0%,#c9c2b0 35%,#e9d9c8 60%,#d7cfc6 100%)}
.arrow{position:absolute;top:230px}
.arrow.left{left:32px}.arrow.right{right:32px}
.search-card{position:absolute;border-radius:12px;color:var(--white);padding:28px 34px}
.nanny-search{left:100px;top:88px;width:420px;height:337px;background:var(--pink)}
.card-head{display:flex;align-items:center;gap:20px;padding-bottom:18px;border-bottom:2px solid rgba(255,255,255,.8)}
.card-head .icon{width:60px;height:60px;border-radius:50%;background:var(--white);flex:none}
.card-head small{display:block;font-size:15px}
.card-head strong{font-family:"Poppins",sans-serif;font-weight:500;font-size:26px;line-height:1.1}
.form-grid{display:grid;grid-template-columns:1fr 1fr;gap:10px 18px;margin-top:20px;font-size:11px}
.field{background:var(--white);color:#444;height:24px;border-radius:2px;padding:4px 8px;position:relative}
.field::after{content:"";position:absolute;right:8px;top:8px;border:4px solid transparent;border-top-color:#666}
.radio-row{display:flex;align-items:center;gap:6px;font-size:11px}
.radio{width:9px;height:9px;border-radius:50%;border:1.5px solid var(--white)}
.radio.on{background:var(--white)}
.card-btn{display:block;margin:18px auto 0;width:106px;text-align:center}

/* about */
.about{position:absolute;top:608px;left:0;width:1200px;height:430px}
.about-copy{position:absolute;left:100px;top:95px;width:520px}
.about-copy p{font-size:13px;line-height:1.9;margin:12px 0 20px}
.family-search{left:677px;top:57px;width:423px;height:305px;background:var(--cyan)}
.family-search .card-head{gap:18px}
.zip{background:var(--white);color:#444;height:28px;border-radius:2px;padding:5px 10px;font-size:12px;margin-top:18px}

/* services */
.services{position:absolute;top:1038px;left:0;width:1200px;height:464px;background:var(--blush)}
.services .head{margin-top:90px}
.service-cards{position:absolute;top:174px;left:138px;display:flex;gap:67px}
.service-card{width:428px;height:204px;background:var(--blush);border:2px solid #f3dcdf;text-align:center;padding:22px 40px;position:relative}
.service-card h3{font-size:24px}
.service-card p{font-size:13px;line-height:1.7;margin:8px 0 12px}
.service-card.nannies h3{color:var(--cyan)}
.service-card.families h3{color:var(--pink)}
.service-card::after{content:"";position:absolute;left:-2px;right:-2px;bottom:-8px;height:7px}
.service-card.nannies::after{background:var(--cyan)}
.service-card.families::after{background:var(--pink)}

/* agency */
.agency{position:absolute;top:1502px;left:0;width:1200px;height:454px}
.agency-copy{position:absolute;left:124px;top:95px;width:580px}
.agency-copy .section-title{font-size:32px}
.agency-copy p{font-size:13px;line-height:1.9;margin:14px 0 22px}
.agency-photo{position:absolute;right:0;top:42px;width:470px;height:412px;background:radial-gradient(circle at 50% 40%,#f1ddc9 0%,#e9e0d5 45%,#cdd86a 80%,#b7c94c 100%);border-radius:200px 0 0 0}

/* benefits */
.benefits{position:absolute;top:1956px;left:0;width:1200px;height:384px;background:linear-gradient(100deg,#d95e6e 0%,#b66878 50%,#6f8ca7 100%);color:var(--white)}
.benefits .eyebrow{color:var(--white);font-size:15px;margin-top:80px}
.benefits h2{font-size:32px;color:var(--white)}
.benefit-row{position:absolute;top:200px;left:200px;width:800px;display:flex;justify-content:space-between}
.benefit{flex:1;text-align:center;font-size:16px;line-height:1.6}
.benefit + .benefit{border-left:2px solid rgba(255,255,255,.7)}
.benefit-icon{width:52px;height:52px;margin:0 auto 12px;border-radius:50%;background:rgba(255,255,255,.9)}

/* testimonials */
.testimonials{position:absolute;top:2340px;left:0;width:1200px;height:392px}
.testimonials .head{margin-top:80px}
.quote{position:absolute;top:186px;display:flex;gap:22px;width:460px}
.quote.one{left:100px}.quote.two{left:642px}
.avatar{flex:none;width:95px;height:95px;border-radius:50%;background:#d8d2cc;border:3px solid var(--white);box-shadow:0 0 0 2px var(--cyan)}
.quote.two .avatar{box-shadow:0 0 0 2px var(--pink)}
.quote p{font-style:italic;font-weight:600;font-size:12.5px;line-height:1.7;color:#333}
.quote .who{text-align:right;font-family:"Poppins",sans-serif;font-size:20px;color:#333;margin-top:12px}
.stars{text-align:right;font-size:15px;letter-spacing:2px;color:var(--cyan)}
.quote.two .stars{color:var(--pink)}

/* faq */
.faq{position:absolute;top:2732px;left:0;width:1200px;height:464px;background:var(--mist)}
.faq-art{position:absolute;left:0;top:58px;width:463px;height:320px;background:linear-gradient(110deg,#b7c94a 0%,#e3418a 50%,#54b9e6 100%);border-radius:0 160px 160px 0;opacity:.9}
.faq-list{position:absolute;left:482px;top:96px;width:642px}
.faq-item{background:var(--white);border:1px solid #ddd;height:40px;margin-bottom:17px;display:flex;align-items:center;justify-content:space-between;padding:0 12px;font-style:italic;font-weight:600;font-size:13.5px;color:#222}
.faq-item .toggle{width:22px;height:22px;border-radius:50%;background:var(--pink);color:var(--white);font-style:normal;text-align:center;line-height:22px;font-size:16px}
.faq-item.open{background:var(--cyan);color:var(--white);border-color:var(--cyan);margin-bottom:0}
.faq-item.open .toggle{background:var(--white);color:var(--cyan)}
.faq-answer{background:var(--white);border:1px solid #ddd;border-top:none;padding:12px;font-size:13px;line-height:1.6;margin-bottom:17px;height:66px}

/* footer */
.site-footer{position:absolute;top:3196px;left:0;width:1200px;height:304px;background:var(--cyan);color:var(--white)}
.foot-col{position:absolute;top:60px}
.foot-col h4{font-size:19px;margin-bottom:18px}
.foot-col ul{list-style:none;font-size:12px;line-height:2}
.contact-col{left:116px;width:220px}
.contact-col li{display:flex;gap:10px;align-items:flex-start;margin-bottom:8px;line-height:1.5}
.links-col{left:364px}
.hours-col{left:549px}
.hours-col td{font-size:12px;padding:4px 14px 4px 0}
.subscribe-col{left:822px;width:280px}
.subscribe{display:flex;height:34px}
.subscribe span{flex:1;background:var(--white);color:#333;font-size:12px;padding:9px 10px}
.subscribe b{background:var(--pink);font-weight:600;font-size:13px;padding:8px 16px}
.social{display:flex;gap:8px;justify-content:flex-end;margin-top:10px}
.social i{width:32px;height:32px;border-radius:3px;background:var(--pink)}
.social i:first-child{background:#3b6fb6}
.social i:last-child{background:#555}
.copyright{position:absolute;top:3500px;left:0;width:1200px;height:64px;background:var(--night);color:#ccc;text-align:center;font-size:12px;line-height:64px}
</style>
</head>
<body>

<header class="site-header">
  <div class="brand"><span class="brand-dot"></span>Bright Pram Hub</div>
  <a class="btn btn-pink join">Join Now</a>
  <nav class="main-nav">
    <span class="active">Home</span><span>About</span><span>Services</span><span>Our Staffs</span><span>Pricing</span><span>Blog</span><span>Contact Us</span>
  </nav>
</header>

<section class="hero">
  <div class="hero-photo" role="img" aria-label="Photo of a mother and young daughter playing with toys at a table"></div>
  <svg class="arrow left" width="20" height="44" viewBox="0 0 20 44"><path d="M18 2 2 22l16 20" fill="none" stroke="#fff" stroke-width="2"/></svg>
  <svg class="arrow right" width="20" height="44" viewBox="0 0 20 44"><path d="M2 2l16 20L2 42" fill="none" stroke="#fff" stroke-width="2"/></svg>
  <div class="search-card nanny-search">
    <div class="card-head"><span class="icon"></span><div><small>Search For The</small><strong>Nanny Near You</strong></div></div>
    <div class="form-grid">
      <div class="radio-row">Gender : <span class="radio on"></span>Male <span class="radio"></span>Female</div>
      <div class="field">Years Of Experience</div>
      <div class="field">Age Range</div>
      <div class="field">Language</div>
      <div class="field">Hourly Rate</div>
      <div class="field">Education</div>
      <div class="radio-row">Certification : <span class="radio on"></span>CPR First Aid</div>
      <div class="radio-row">Transport : <span class="radio on"></span>Yes <span class="radio"></span>No</div>
    </div>
    <a class="btn btn-cyan card-btn">Search</a>
  </div>
</section>

<section class="about">
  <div class="about-copy">
    <div class="eyebrow">A Little</div>
    <h2 class="section-title">About Us</h2>
    <p>Lorem ipsum dolor sit amet, consectetur adipiscing elit, sed do eiusmuiy od tempor incididunt ut labore et dolore magna aliqua. Ut enim ad minim veniam, quis nostruid exercitation ullamco laboris nisi ut aliquip ex ea commodo consequat. Lorem ipsum dolor sit amet, consectet ut la quis nostrud exercitatio aliqua.</p>
    <a class="btn btn-pink">Learn More</a>
  </div>
  <div class="search-card family-search">
    <div class="card-head"><span class="icon"></span><div><small>Search For The</small><strong>Families By Location</strong></div></div>
    <div class="zip">Enter The Zip</div>
    <div class="form-grid">
      <div class="radio-row">Gender : <span class="radio on"></span>Male <span class="radio"></span>Female</div>
      <div class="field">Age Range</div>
      <div class="field">Take Care During</div>
      <div class="field">Special Needs</div>
    </div>
    <a class="btn btn-pink card-btn">Search</a>
  </div>
</section>

<section class="services">
  <div class="head center"><div class="eyebrow">What We Offer</div><h2 class="section-title">Our Services</h2></div>
  <div class="service-cards">
    <article class="service-card nannies">
      <h3>For Nannies</h3>
      <p>Praesent ac purus turpis. Curabitur congue ex sem, sit amet scelerisque nisi convallis non. Viva mus rutrum imperdiet sodales.</p>
      <a class="btn btn-cyan">Learn More</a>
    </article>
    <article class="service-card families">
      <h3>For Families</h3>
      <p>Praesent ac purus turpis. Curabitur congue ex sem, sit amet scelerisque nisi convallis non. Viva mus rutrum imperdiet sodales.</p>
      <a class="btn btn-pink">Learn More</a>
    </article>
  </div>
</section>

<section class="agency">
  <div class="agency-photo" role="img" aria-label="Photo of a smiling woman holding a baby on a green exercise ball"></div>
  <div class="agency-copy">
    <div class="eyebrow">Bright Pram Hub</div>
    <h2 class="section-title">We Are More Than Just a<br>Nanny Agency</h2>
    <p>Lorem ipsum dolor sit amet, consectetur adipiscing elit, sed do eiusmuiy od tempor incididunt ut labore et dolore magna aliqua. Ut enim ad minim veniam, quis nostruid exercitation ullamco laboris nisi ut aliquip ex ea commodo consequat. Lorem ipshjyu uikam oris nisi ut aliquip ex ea commodo dolor sit amet, consectet ut la quis nostrud exercitatio aliqua.</p>
    <a class="btn btn-pink">Learn More</a>
  </div>
</section>

<section class="benefits center">
  <div class="eyebrow">Our Benefits</div>
  <h2>Why Choose Us</h2>
  <div class="benefit-row">
    <div class="benefit"><div class="benefit-icon" role="img" aria-label="Money bag icon"></div>Reduced Cost</div>
    <div class="benefit"><div class="benefit-icon" role="img" aria-label="Children playing icon"></div>Increased Socialization<br>With Other Children</div>
    <div class="benefit"><div class="benefit-icon" role="img" aria-label="Falling chart icon"></div>Reduced Illness</div>
    <div class="benefit"><div class="benefit-icon" role="img" aria-label="Parents icon"></div>Increased Flexibility<br>For Parents</div>
  </div>
</section>

<section class="testimonials">
  <div class="head center"><div class="eyebrow">Testimonials</div><h2 class="section-title">What Our Families Say</h2></div>
  <article class="quote one">
    <div class="avatar" role="img" aria-label="Portrait of a parent"></div>
    <div><p>Lorem ipsum dolor sit amet, consectetur adipiscing elit, sed dko eiusmod tempor incididunt ut labore et dolore mullamco laboris nisi utmodo consequat.</p><div class="who">- Marisol</div><div class="stars">★★★★★</div></div>
  </article>
  <article class="quote two">
    <div class="avatar" role="img" aria-label="Portrait of a parent"></div>
    <div><p>Lorem ipsum dolor sit amet, consectetur adipiscing elit, sed dko eiusmod tempor incididunt ut labore et dolore mullamco laboris nisi utmodo consequat.</p><div class="who">- Marisol</div><div class="stars">★★★★★</div></div>
  </article>
</section>

<section class="faq">
  <div class="faq-art" role="img" aria-label="Illustration of overlapping speech bubbles spelling FAQ"></div>
  <div class="faq-list">
    <div class="faq-item open">Lorem Ipsum is simply dummy text of the printing and typesetting industry.<span class="toggle">–</span></div>
    <div class="faq-answer">There are many variations of passages of Lorem Ipsum available, but the majority have suffered alteration in some form, by injected humour.</div>
    <div class="faq-item">Lorem Ipsum is simply dummy text of the printing and typesetting industry.<span class="toggle">+</span></div>
    <div class="faq-item">Lorem Ipsum is simply dummy text of the printing and typesetting industry.<span class="toggle">+</span></div>
    <div class="faq-item">Lorem Ipsum is simply dummy text of the printing and typesetting industry.<span class="toggle">+</span></div>
  </div>
</section>

<footer class="site-footer">
  <div class="foot-col contact-col">
    <h4>Contact Us</h4>
    <ul>
      <li><svg width="10" height="14" viewBox="0 0 10 14"><path d="M5 0a5 5 0 0 0-5 5c0 4 5 9 5 9s5-5 5-9a5 5 0 0 0-5-5zm0 7a2 2 0 1 1 0-4 2 2 0 0 1 0 4z" fill="#fff"/></svg><span>001 Lorem Ipsum, Dolor Sit,<br>Amet - 000001</span></li>
      <li><svg width="12" height="12" viewBox="0 0 12 12"><path d="M2.5 0 4.5 3 3.2 4.5a7 7 0 0 0 4.3 4.3L9 7.5l3 2-1.5 2.5C5 12 0 7 0 1.5z" fill="#fff"/></svg><span>+1 555 010 2040</span></li>
      <li><svg width="13" height="10" viewBox="0 0 13 10"><rect x=".5" y=".5" width="12" height="9" fill="none" stroke="#fff"/><path d="M.5.5 6.5 5l6-4.5" fill="none" stroke="#fff"/></svg><span>info@brightpramhub.net</span></li>
    </ul>
  </div>
  <div class="foot-col links-col">
    <h4>Useful Links</h4>
    <ul><li>Home</li><li>About</li><li>Services</li><li>Our Staffs</li><li>Pricing</li><li>Blog</li><li>Contact Us</li></ul>
  </div>
  <div class="foot-col hours-col">
    <h4>Opening Hours</h4>
    <table><tr><td>Mon - Thurs :</td><td>10:00 am - 8:00 pm</td></tr><tr><td>Fri - Sat :</td><td>11:00 am - 8:00 pm</td></tr><tr><td>Sun :</td><td>Closed</td></tr></table>
  </div>
  <div class="foot-col subscribe-col">
    <h4>Subscribe Us</h4>
    <div class="subscribe"><span>Enter Your Email</span><b>Submit</b></div>
    <div class="social"><i></i><i></i><i></i></div>
  </div>
</footer>
<div class="copyright">Copyright © 2018 . All rights reserved.</div>

</body>
</html>
```